Professional & attention grabbing.

A business card design, front and back. I already have a logo I will attach, but I am open to something new as well.
Things to include:
Name:
Title:
Phone:
Email:
Wanting something that is professional but attention grabbing.
Also we do a lot of work using drones on natural gas pipelines (leading the future)if you want to include any of that. I'm open to ideas.
Target Market(s)
Natural gas transmission industry / greenhouse gas mitigation industry
Industry/Entity Type
Business
Colors
Designer to choose colors to be used in the design.
Look and feel
Each slider illustrates characteristics of the customer's brand and the style your logo design should communicate.

```html
<!DOCTYPE html>
<html lang="en">
<head>
<meta charset="utf-8">
<title>Vantline – Business Card</title>
<link rel="stylesheet" href="https://fonts.googleapis.com/css2?family=Open+Sans:wght@400;600;700;800&display=swap">
<style>
  :root {
    --backdrop: #5b4b3d;
    --card-white: #ffffff;
    --brand-red: #c11f24;
    --charcoal: #3a3a3c;
    --ink-light: #f2f2f2;
  }
  * { margin: 0; padding: 0; box-sizing: border-box; }
  html, body {
    width: 1200px; height: 987px; overflow: hidden;
    background: var(--backdrop);
    font-family: "Open Sans", sans-serif;
  }
  .canvas { position: relative; width: 1200px; height: 987px; }
  .card {
    position: absolute; left: 293px; width: 615px; height: 352px;
    box-shadow: 0 2px 4px rgba(0,0,0,0.35);
  }
  .card-front { top: 130px; background: var(--card-white); }
  .card-back { top: 506px; background: var(--brand-red); }

  .accent-bar {
    position: absolute; left: 0; top: 73px; width: 14px; height: 198px;
    background: var(--brand-red);
  }
  .brand {
    position: absolute; left: 64px; top: 150px; height: 50px;
    display: flex; align-items: center; gap: 12px;
  }
  .brand-square { width: 44px; height: 44px; background: var(--brand-red); flex: none; }
  .brand-name {
    font-weight: 800; font-size: 30px; letter-spacing: -0.3px;
    color: var(--charcoal); line-height: 1; white-space: nowrap;
  }

  .contact-panel {
    position: absolute; left: 351px; top: 73px; width: 264px; height: 198px;
    background: var(--charcoal); padding: 28px 0 0 31px; color: var(--ink-light);
  }
  .person-name {
    font-size: 20px; font-weight: 600; color: var(--brand-red);
    text-transform: uppercase; line-height: 1.1; white-space: nowrap;
  }
  .person-title { font-size: 16px; margin-top: 4px; }
  .contact-list { list-style: none; margin-top: 16px; }
  .contact-list li {
    display: flex; align-items: center; gap: 8px;
    font-size: 15.5px; line-height: 23px; white-space: nowrap;
  }
  .contact-icon { width: 14px; height: 14px; flex: none; }

  .back-mark {
    position: absolute; left: 0; right: 0; top: 143px;
    display: flex; justify-content: center; align-items: center; gap: 16px;
  }
  .back-square { width: 60px; height: 60px; background: var(--card-white); flex: none; }
  .back-name {
    font-weight: 800; font-size: 56px; color: var(--card-white); line-height: 1;
  }
  .back-url {
    position: absolute; left: 0; right: 0; top: 302px; text-align: center;
    color: var(--card-white); font-style: italic; font-size: 16px; letter-spacing: 5px;
  }
</style>
</head>
<body>
<main class="canvas">
  <section class="card card-front">
    <div class="accent-bar"></div>
    <div class="brand">
      <span class="brand-square"></span>
      <span class="brand-name">VANTLINE</span>
    </div>
    <div class="contact-panel">
      <p class="person-name">Dana Whitfield</p>
      <p class="person-title">CEO/Founder</p>
      <ul class="contact-list">
        <li>
          <svg class="contact-icon" viewBox="0 0 24 24" aria-hidden="true"><path fill="#c11f24" d="M6.6 10.8a15.1 15.1 0 0 0 6.6 6.6l2.2-2.2c.3-.3.7-.4 1-.2 1.1.4 2.3.6 3.6.6.6 0 1 .4 1 1V20c0 .6-.4 1-1 1A17 17 0 0 1 3 4c0-.6.4-1 1-1h3.5c.6 0 1 .4 1 1 0 1.3.2 2.5.6 3.6.1.3 0 .7-.2 1z"/></svg>
          555 014 2290
        </li>
        <li>
          <svg class="contact-icon" viewBox="0 0 24 24" aria-hidden="true"><path fill="#c11f24" d="M2 5h20v14H2z"/><path fill="none" stroke="#3a3a3c" stroke-width="2" d="M2 6l10 7 10-7"/></svg>
          dana@vantline.com
        </li>
        <li>
          <svg class="contact-icon" viewBox="0 0 24 24" aria-hidden="true"><circle cx="12" cy="12" r="10" fill="#c11f24"/><path fill="none" stroke="#3a3a3c" stroke-width="1.6" d="M2 12h20M12 2c3 3 3 17 0 20M12 2c-3 3-3 17 0 20"/></svg>
          www.vantline.com
        </li>
      </ul>
    </div>
  </section>

  <section class="card card-back">
    <div class="back-mark">
      <span class="back-square"></span>
      <span class="back-name">VANTLINE</span>
    </div>
    <p class="back-url">www.vantline.com</p>
  </section>
</main>
</body>
</html>
```